Trailer Lettering or Partial Wrap

I purchased a new gloss black 7' wide x 12' long x 7' height enclosed cargo trailer that I would like to brand for advertising. on all 4 sides. Our font is AgencyFB (and we only use lower case letters). To reduce cost I thought using the black gloss background could be achieved and use cut out vinyl rather than full wrap unless there are some other ideas. Our colors are Black, White, and Red (HEX #BE1E2D. Items to be displayed:
- logo
- phone # (405) 555-2716
- email. catering@kelpcornerok.com
- web address: www.kelpcornerok.com
- our 2 restaurant locations
- "Edmond" 4875 NE 92nd, Edmond OK 73099
- "NW-OKC" 2719 E Larkspur Ave, Oklahoma City, OK 73198

we would also like to highlight 3 services we offer:
- Catering
- Rent-A-Chef Events
- Sushi Making Classes

For reference our chopsticks from the logo files we use on a lot of print items. Not that I want it to be like this, but I did attach a sample of what ChatGPT created though is in an unusable format and fonts aren't consistent. As well a recent 2' x 4' sign we had made to use on table displays.

We also do like the wording on that last item of " Sushi | Experience | Elevated"

```html
<!DOCTYPE html>
<html lang="en">
<head>
<meta charset="utf-8">
<title>Kelp Corner – Trailer Side Lettering</title>
<link href="https://fonts.googleapis.com/css2?family=Saira+Extra+Condensed:wght@300;400;500&display=swap" rel="stylesheet">
<style>
  :root {
    --stage: #cccccc;
    --black: #000000;
    --white: #ffffff;
    --red: #be1e2d;
    --bright-red: #e0141e;
    --frame: #c9c9c9;
    --icon-fill: #2a2a2a;
    --type: "Saira Extra Condensed", "Arial Narrow", "Liberation Sans Narrow", sans-serif;
  }
  * { margin: 0; padding: 0; box-sizing: border-box; }
  html, body { width: 1200px; height: 1001px; overflow: hidden; background: var(--stage); }
  .canvas { position: relative; width: 1200px; height: 1001px; background: var(--stage); font-family: var(--type); }
  .trailer-side {
    position: absolute; left: 76px; top: 226px; width: 812px; height: 440px;
    background: var(--black); color: var(--white); overflow: hidden;
  }
  .trailer-side div { white-space: nowrap; }

  /* brand lockup */
  .brand { position: absolute; border-radius: 50%; border: 7px solid var(--bright-red);
    display: flex; align-items: center; justify-content: center; }
  .brand-name { font-weight: 500; color: var(--white); text-transform: lowercase; line-height: 0.9; text-align: left; }
  .brand-main { left: 42px; top: 54px; width: 168px; height: 168px; }
  .brand-main .brand-name { font-size: 44px; }
  .brand-door { left: 598px; top: 192px; width: 108px; height: 108px; border-width: 5px; }
  .brand-door .brand-name { font-size: 28px; }

  /* services */
  .service { position: absolute; left: 260px; display: flex; align-items: center; gap: 10px; }
  .service-icon { width: 40px; height: 40px; flex: none; }
  .service-label { font-size: 13px; line-height: 1.05; text-transform: lowercase; }
  .service-rule { position: absolute; left: 264px; width: 102px; height: 1px; background: var(--red); }

  /* tagline */
  .tagline-row { position: absolute; left: 409px; display: flex; align-items: center; gap: 9px; }
  .tagline-bar { width: 2px; height: 30px; background: var(--red); }
  .tagline-word { font-size: 26px; line-height: 1; text-transform: lowercase; }

  .divider { position: absolute; left: 40px; top: 256px; width: 490px; height: 1px; background: var(--red); }

  /* locations */
  .location { position: absolute; top: 280px; font-size: 12px; line-height: 18px; }
  .location-name { color: var(--bright-red); font-weight: 300; }

  /* contact */
  .contact { position: absolute; left: 300px; display: flex; align-items: center; gap: 8px; }
  .contact-icon { width: 22px; height: 22px; flex: none; }
  .contact-line { font-size: 17px; line-height: 1; }
  .web-band {
    position: absolute; left: 276px; top: 354px; width: 268px; height: 24px; background: var(--bright-red);
    color: var(--black); font-size: 20px; line-height: 24px; text-align: center;
  }

  /* door */
  .door-frame { position: absolute; left: 562px; top: 69px; width: 179px; height: 353px; background: var(--frame); }
  .door-panel { position: absolute; left: 576px; top: 82px; width: 152px; height: 328px; background: var(--black); }
</style>
</head>
<body>
<main class="canvas">
  <section class="trailer-side">

    <div class="brand brand-main"><div class="brand-name">kelp<br>corner</div></div>

    <!-- services -->
    <div class="service" style="top:54px">
      <svg class="service-icon" viewBox="0 0 40 40" role="img" aria-label="catering cloche icon"><circle cx="20" cy="20" r="18" fill="none" stroke="#e0141e" stroke-width="2.5"/><circle cx="20" cy="20" r="9" fill="#2a2a2a"/></svg>
      <div class="service-label">catering</div>
    </div>
    <div class="service-rule" style="top:103px"></div>

    <div class="service" style="top:116px">
      <svg class="service-icon" viewBox="0 0 40 40" role="img" aria-label="chef hat icon"><circle cx="20" cy="20" r="18" fill="none" stroke="#e0141e" stroke-width="2.5"/><circle cx="20" cy="20" r="9" fill="#2a2a2a"/></svg>
      <div class="service-label">rent-a-chef<br>events</div>
    </div>
    <div class="service-rule" style="top:166px"></div>

    <div class="service" style="top:178px">
      <svg class="service-icon" viewBox="0 0 40 40" role="img" aria-label="sushi rolls icon"><circle cx="20" cy="20" r="18" fill="none" stroke="#e0141e" stroke-width="2.5"/><circle cx="20" cy="20" r="9" fill="#2a2a2a"/></svg>
      <div class="service-label">sushi making<br>classes</div>
    </div>

    <!-- tagline -->
    <div class="tagline-row" style="top:84px"><span class="tagline-bar"></span><span class="tagline-word">sushi</span></div>
    <div class="tagline-row" style="top:123px"><span class="tagline-bar"></span><span class="tagline-word">experience</span></div>
    <div class="tagline-row" style="top:160px"><span class="tagline-bar"></span><span class="tagline-word">elevated</span></div>

    <div class="divider"></div>

    <!-- locations -->
    <div class="location" style="left:41px">
      <div class="location-name">Edmond</div>
      <div>4875 NE 92nd,</div>
      <div>Edmond, OK 73099</div>
    </div>
    <div class="location" style="left:154px">
      <div class="location-name">NW-OKC</div>
      <div>2719 E Larkspur Ave,</div>
      <div>Oklahoma City, OK 73198</div>
    </div>

    <!-- contact -->
    <div class="contact" style="top:278px">
      <svg class="contact-icon" viewBox="0 0 32 32"><circle cx="16" cy="16" r="13.5" fill="none" stroke="#e0141e" stroke-width="2"/><path d="M11 9.5l3 0 1 3.5-2 1.5c1 2 2.5 3.5 4.5 4.5l1.5-2 3.5 1v3c-6 1-12.5-5.5-11.5-11.5z" fill="#fff"/></svg>
      <div class="contact-line">(405) 555-2716</div>
    </div>
    <div class="contact" style="top:312px">
      <svg class="contact-icon" viewBox="0 0 32 32"><circle cx="16" cy="16" r="13.5" fill="none" stroke="#e0141e" stroke-width="2"/><rect x="9.5" y="11" width="13" height="10" fill="none" stroke="#fff" stroke-width="1.6"/><path d="M9.5 11l6.5 5.5 6.5-5.5" fill="none" stroke="#fff" stroke-width="1.6"/></svg>
      <div class="contact-line">catering@kelpcornerok.com</div>
    </div>

    <div class="web-band">www.kelpcornerok.com</div>

    <!-- door -->
    <div class="door-frame"></div>
    <div class="door-panel"></div>
    <div class="brand brand-door"><div class="brand-name">kelp<br>corner</div></div>

  </section>
</main>
</body>
</html>
```